Brightway Haul & Upkeep Services, are a company that offers a 'one stop shop' pre-move clean up a

I have already selected a logo which I would like on the front of the business cards along with phone numbers, web address and email which are:
0487650392
www.brightwayhaul.com.au
brightwayhaulandupkeep@mailbox.example

On the back of the card I would like to list some of the types of service we offer (clean - move - repairs/maintenance) which are:
CLEAN - windows, gutters, solar panels, driveways/paths, carpets.
MOVE - Small/medium size house/office moves, large item pick-up & delivery, yard clean-up and removal.
General maintenance and repairs.

I would like the blue logo on a gray background.

Thanks

```html
<!DOCTYPE html>
<html lang="en">
<head>
<meta charset="utf-8">
<title>Brightway Haul &amp; Upkeep Services – Business Cards</title>
<link rel="stylesheet" href="https://fonts.googleapis.com/css2?family=Open+Sans:wght@400;600;800&display=swap">
<style>
  :root {
    --backdrop: #e9e6e2;
    --card-light: #f4f4f5;
    --card-mid: #d9dadc;
    --card-dark: #b9bbbe;
    --brand-blue: #2f74c0;
    --ink: #1f1f21;
    --paper-white: #ffffff;
  }
  * { box-sizing: border-box; margin: 0; padding: 0; }
  html, body {
    width: 1200px;
    height: 790px;
    overflow: hidden;
    background: var(--backdrop);
    font-family: "Open Sans", Arial, sans-serif;
  }
  .sheet {
    position: relative;
    width: 1200px;
    height: 790px;
  }
  .card {
    position: absolute;
    top: 235px;
    width: 540px;
    height: 320px;
    border-radius: 26px;
    overflow: hidden;
    background: linear-gradient(160deg, var(--card-light) 0%, var(--card-mid) 55%, var(--card-dark) 100%);
    box-shadow: 0 10px 24px rgba(0,0,0,0.25);
  }
  .card--front { left: 40px; }
  .card--back { left: 620px; }

  .brand-name {
    color: var(--brand-blue);
    font-weight: 800;
    font-size: 34px;
    line-height: 1.08;
    letter-spacing: 0.5px;
    text-transform: uppercase;
  }
  .card--front .brand-name {
    position: absolute;
    top: 44px;
    left: 70px;
  }
  .card--back .brand-name {
    position: absolute;
    top: 40px;
    left: 0;
    right: 0;
    text-align: center;
  }

  .contact-list {
    position: absolute;
    left: 32px;
    top: 160px;
    list-style: none;
    font-size: 13px;
    color: var(--ink);
  }
  .contact-list li {
    display: flex;
    align-items: center;
    gap: 8px;
    margin-bottom: 12px;
  }
  .contact-icon { width: 13px; height: 13px; flex: none; }

  .wave { position: absolute; left: 0; top: 0; width: 540px; height: 320px; }
  .web-address {
    position: absolute;
    right: 24px;
    top: 212px;
    transform: rotate(-13deg);
    transform-origin: right center;
    color: var(--paper-white);
    font-weight: 600;
    font-size: 14px;
    letter-spacing: 2px;
    white-space: nowrap;
  }

  .services-heading {
    position: absolute;
    top: 150px;
    left: 0;
    right: 0;
    text-align: center;
    color: var(--brand-blue);
    font-weight: 600;
    font-size: 21px;
    letter-spacing: 7px;
  }
  .services-list {
    position: absolute;
    top: 192px;
    left: 0;
    right: 0;
    list-style: none;
    text-align: center;
    color: var(--ink);
    font-weight: 600;
    font-size: 18px;
    line-height: 1.55;
  }
  .services-list .pair span { margin: 0 14px; }
  .services-list li::before,
  .services-list .pair span::before { content: "• "; color: var(--brand-blue); }
  .services-list .pair::before { content: none; }
</style>
</head>
<body>
<main class="sheet">

  <section class="card card--front" aria-label="Business card front">
    <svg class="wave" viewBox="0 0 540 320" aria-hidden="true">
      <path d="M0 292 C 200 280, 380 250, 540 160 L540 320 L0 320 Z" fill="var(--brand-blue)"/>
      <path d="M80 274 C 230 262, 390 236, 540 148" fill="none" stroke="var(--ink)" stroke-width="3"/>
    </svg>

    <h1 class="brand-name">Brightway Haul<br>&amp; Upkeep Services</h1>

    <ul class="contact-list">
      <li>
        <svg class="contact-icon" viewBox="0 0 16 16" aria-hidden="true"><circle cx="8" cy="8" r="7" fill="none" stroke="var(--brand-blue)" stroke-width="1.5"/><path d="M5.5 4.5 l1.5 0 l0.6 2 l-1 0.8 a5 5 0 0 0 2.2 2.2 l0.8 -1 l2 0.6 l0 1.5 a1 1 0 0 1 -1 1 a7 7 0 0 1 -6 -6 a1 1 0 0 1 0.9 -1.1 z" fill="var(--brand-blue)"/></svg>
        <span>0487650392</span>
      </li>
      <li>
        <svg class="contact-icon" viewBox="0 0 16 16" aria-hidden="true"><rect x="1.5" y="4" width="13" height="9" rx="1" fill="none" stroke="var(--brand-blue)" stroke-width="1.5"/><path d="M1.5 4.5 L8 9 L14.5 4.5" fill="none" stroke="var(--brand-blue)" stroke-width="1.5"/></svg>
        <span>brightwayhaulandupkeep@mailbox.example</span>
      </li>
    </ul>

    <p class="web-address">www.brightwayhaul.com.au</p>
  </section>

  <section class="card card--back" aria-label="Business card back">
    <h2 class="brand-name">Brightway Haul<br>&amp; Upkeep Services</h2>
    <p class="services-heading">Services we offer</p>
    <ul class="services-list">
      <li class="pair"><span>Clean</span><span>Move</span></li>
      <li>General maintenance and repairs.</li>
    </ul>
  </section>

</main>
</body>
</html>
```